Visitenkarten-Design für Boutique-Unternehmensberatung
Zielgruppe
Boutique Unternehmensberatung für die Chemische Industrie. Wir unterstützen Unternehmen, die Beziehung zu Ihren Händlern zu optimieren.
Vorläufige Website vertriebsbruecke-online.de kann ggf weitere Einblicke geben. Hinweis: Diese Website wurde bisher noch nicht professionell erstellt.
Aufgabenstellung
Die Visitenkarte sollte vertrauenserweckend und seriös wirken. Zeitgleich aber auch modern.

```html
<!DOCTYPE html>
<html lang="de">
<head>
<meta charset="utf-8">
<title>Visitenkarte – Vertriebsbrücke</title>
<link href="https://fonts.googleapis.com/css2?family=Montserrat:wght@400;500;700&display=swap" rel="stylesheet">
<style>
  :root {
    --brand-blue: #0f5594;
    --paper-white: #ffffff;
    --backdrop: #c9cacd;
    --photo-light: #c9b8aa;
    --photo-dark: #8a97a8;
  }
  * { box-sizing: border-box; margin: 0; padding: 0; }
  html, body { width: 1200px; height: 852px; overflow: hidden; }
  body {
    background: var(--backdrop);
    font-family: "Montserrat", sans-serif;
    color: var(--brand-blue);
    position: relative;
  }
  .card {
    position: absolute;
    top: 258px;
    width: 520px;
    height: 336px;
    border-radius: 3px;
    overflow: hidden;
  }
  .card-front { left: 50px; background: var(--brand-blue); }
  .card-back { left: 630px; background: var(--paper-white); }

  .wordmark {
    display: flex;
    align-items: center;
    gap: 10px;
    font-weight: 700;
  }
  .wordmark-dot { border-radius: 50%; flex: none; }
  .card-front .wordmark {
    position: absolute; left: 0; right: 0; top: 148px;
    justify-content: center;
    color: var(--paper-white);
    font-size: 30px;
  }
  .card-front .wordmark-dot { width: 30px; height: 30px; background: var(--paper-white); }

  .holder {
    position: absolute; left: 36px; top: 32px;
    display: flex; align-items: baseline; gap: 10px;
    white-space: nowrap;
  }
  .holder-name { font-size: 27px; font-weight: 700; }
  .holder-sep { font-size: 18px; font-weight: 700; }
  .holder-role { font-size: 17px; font-weight: 400; }

  .contact-row {
    position: absolute; left: 36px; top: 80px;
    display: flex; gap: 26px;
    font-size: 12.5px;
  }
  .contact-item { display: flex; align-items: center; gap: 7px; white-space: nowrap; }
  .icon { width: 14px; height: 14px; flex: none; }

  .band {
    position: absolute; top: 150px; height: 24px;
    background: var(--brand-blue);
  }
  .band-left { left: 0; width: 62px; }
  .band-right { left: 160px; width: 108px; }
  .portrait {
    position: absolute; left: 58px; top: 112px;
    width: 104px; height: 104px; border-radius: 50%;
    border: 4px solid var(--paper-white);
    background: radial-gradient(circle at 45% 45%, var(--photo-light), var(--photo-dark));
  }

  .company {
    position: absolute; left: 282px; top: 134px; right: 14px;
    font-size: 11px; line-height: 1.6;
  }
  .company-name { font-weight: 700; }
  .company-links { margin-top: 12px; display: flex; flex-direction: column; gap: 3px; }
  .company .icon { width: 13px; height: 13px; }
  .company .contact-item { gap: 6px; }

  .card-back .wordmark {
    position: absolute; left: 58px; top: 262px;
    font-size: 17px; gap: 8px;
  }
  .card-back .wordmark-dot { width: 18px; height: 18px; background: var(--brand-blue); }
</style>
</head>
<body>

<section class="card card-front" aria-label="Vorderseite">
  <div class="wordmark">
    <span class="wordmark-dot"></span>
    <span class="wordmark-name">Vertriebsbrücke</span>
  </div>
</section>

<section class="card card-back" aria-label="Rückseite">
  <div class="holder">
    <span class="holder-name">Jonas Albrecht</span>
    <span class="holder-sep">•</span>
    <span class="holder-role">Geschäftsführer / CEO</span>
  </div>

  <div class="contact-row">
    <span class="contact-item">
      <svg class="icon" viewBox="0 0 14 14" aria-hidden="true"><circle cx="7" cy="7" r="7" fill="#0f5594"/><path d="M4.6 3.6l1.3-.2.6 1.7-.8.7c.4.9 1 1.5 1.9 1.9l.7-.8 1.7.6-.2 1.3c-3 .2-5.4-2.2-5.2-5.2z" fill="#fff"/></svg>
      +49 6150 / 12 34 56 78
    </span>
    <span class="contact-item">
      <svg class="icon" viewBox="0 0 14 14" aria-hidden="true"><circle cx="7" cy="7" r="7" fill="#0f5594"/><rect x="3.6" y="4.6" width="6.8" height="4.8" fill="none" stroke="#fff" stroke-width="1"/><path d="M3.6 4.8L7 7.4l3.4-2.6" fill="none" stroke="#fff" stroke-width="1"/></svg>
      ja@vertriebsbruecke-online.de
    </span>
  </div>

  <div class="band band-left"></div>
  <div class="band band-right"></div>
  <div class="portrait" role="img" aria-label="Porträtfoto des Geschäftsführers"></div>

  <div class="company">
    <p class="company-name">JAB Vertriebsbrücke<br>GmbH i.G.</p>
    <p>Lindenweg 4<br>64283 Musterstadt</p>
    <div class="company-links">
      <span class="contact-item">
        <svg class="icon" viewBox="0 0 14 14" aria-hidden="true"><circle cx="7" cy="7" r="7" fill="#0f5594"/><path d="M4.6 3.6l1.3-.2.6 1.7-.8.7c.4.9 1 1.5 1.9 1.9l.7-.8 1.7.6-.2 1.3c-3 .2-5.4-2.2-5.2-5.2z" fill="#fff"/></svg>
        +49 6150 / 12 34 56 70
      </span>
      <span class="contact-item">
        <svg class="icon" viewBox="0 0 14 14" aria-hidden="true"><circle cx="7" cy="7" r="7" fill="#0f5594"/><rect x="3.6" y="4.6" width="6.8" height="4.8" fill="none" stroke="#fff" stroke-width="1"/><path d="M3.6 4.8L7 7.4l3.4-2.6" fill="none" stroke="#fff" stroke-width="1"/></svg>
        info@vertriebsbruecke-online.de
      </span>
      <span class="contact-item">
        <svg class="icon" viewBox="0 0 14 14" aria-hidden="true"><circle cx="7" cy="7" r="7" fill="#0f5594"/><circle cx="7" cy="7" r="3.6" fill="none" stroke="#fff" stroke-width="0.9"/><ellipse cx="7" cy="7" rx="1.5" ry="3.6" fill="none" stroke="#fff" stroke-width="0.9"/><path d="M3.4 7h7.2" stroke="#fff" stroke-width="0.9"/></svg>
        www.vertriebsbruecke-online.de
      </span>
    </div>
  </div>

  <div class="wordmark">
    <span class="wordmark-dot"></span>
    <span class="wordmark-name">Vertriebsbrücke</span>
  </div>
</section>

</body>
</html>
```